"Vine Hollow Excursions" is a top notch Santa Barbara County Wine Tour company.

We provide scenic, boutique and custom wine tours. I need the card to be clean and classy. I will provide our logo. I would like the logo to cover the back side of the card as an option and would like to see a couple color options other then our signature green and gold. I would like to see some creative options and let the designers come up with options.
I need cards for myself and my team. The final design should communicate "An authentic and boutique wine tour experience"
Please use my website for reference www.vinehollowexcursions.example

Target Market(s)

We have a wide range of clients from millennials to baby boomers

Industry/Entity Type

Tour

Contact Information for Business Card

Contact info:
Dale Morton
805-219-6384
info@vinehollowexcursions.example
vinehollowexcursions.example

Colors

Designer to choose colors to be used in the design.

Requirements
Must have
• my logo
Nice to have
• *I would like to have the backside side with the logo and the company statement
• "An authentic and boutique wine tour experience" as an option.
• *I would also like to see what the designers can create!
• *I would like to see an option that incorporates or social: instagram, yelp, Trip Planner
Should not have
• I do not want it too busy.

```html
<!DOCTYPE html>
<html lang="en">
<head>
<meta charset="utf-8">
<title>Vine Hollow Excursions – Business Card</title>
<link href="https://fonts.googleapis.com/css2?family=Cinzel:wght@600&family=Montserrat:wght@400;500&display=swap" rel="stylesheet">
<style>
  :root {
    --backdrop: #e4e4e2;
    --paper: #ffffff;
    --vine-green: #436b4b;
    --gold-soft: #d9c8b0;
    --ink-light: #f4f1ea;
  }
  * { box-sizing: border-box; margin: 0; padding: 0; }
  html, body { width: 1200px; height: 810px; overflow: hidden; }
  body {
    background: var(--backdrop);
    position: relative;
    font-family: "Montserrat", sans-serif;
  }
  .card {
    position: absolute;
    width: 560px;
    height: 320px;
    background: var(--paper);
    box-shadow: 0 10px 28px rgba(0,0,0,0.18);
    overflow: hidden;
  }
  .card--front { left: 70px; top: 70px; display: flex; align-items: center; justify-content: center; }
  .card--back { left: 570px; top: 420px; }

  .brand-name {
    font-family: "Montserrat", sans-serif;
    font-weight: 500;
    color: var(--vine-green);
    display: flex;
    align-items: center;
    gap: 12px;
    white-space: nowrap;
  }
  .brand-name__dot {
    width: 14px; height: 14px; border-radius: 50%;
    background: var(--vine-green);
    flex-shrink: 0;
  }
  .card--front .brand-name { font-size: 28px; }
  .card--back .brand-name { position: absolute; right: 26px; top: 34px; font-size: 15px; gap: 8px; }
  .card--back .brand-name__dot { width: 9px; height: 9px; }

  .holder {
    position: absolute; left: 0; top: 110px;
    padding-left: 22px;
    border-left: 8px solid var(--vine-green);
  }
  .holder__name {
    font-family: "Cinzel", serif; font-weight: 600;
    font-size: 22px; color: var(--vine-green); letter-spacing: 1px; line-height: 1.1;
  }
  .holder__role {
    font-size: 13px; color: var(--vine-green); letter-spacing: 1px; text-transform: uppercase;
  }

  .rule-thin { position: absolute; left: 0; right: 0; top: 156px; height: 3px; background: var(--vine-green); }
  .green-band { position: absolute; left: 0; right: 0; top: 166px; bottom: 0; background: var(--vine-green); }

  .socials {
    position: absolute; right: 20px; top: 178px;
    text-align: right; color: var(--ink-light);
    font-size: 12.5px; line-height: 1.45;
  }
  .socials__title { font-size: 13px; letter-spacing: 1px; text-transform: uppercase; }
  .socials__row { display: flex; justify-content: flex-end; align-items: center; gap: 8px; }
  .socials__mark { width: 9px; height: 9px; border-radius: 50%; background: var(--gold-soft); }

  .contacts {
    position: absolute; left: 26px; bottom: 22px;
    color: var(--ink-light); font-size: 13px; line-height: 1.55;
  }
  .contacts__row { display: flex; align-items: center; gap: 12px; }
  .contacts__icon { width: 16px; height: 16px; flex-shrink: 0; }
  .contacts__site strong { font-weight: 500; }
</style>
</head>
<body>

  <section class="card card--front">
    <div class="brand-name"><span class="brand-name__dot"></span>Vine Hollow Excursions</div>
  </section>

  <section class="card card--back">
    <div class="brand-name"><span class="brand-name__dot"></span>Vine Hollow Excursions</div>

    <div class="holder">
      <p class="holder__name">DALE MORTON</p>
      <p class="holder__role">Trip Planner</p>
    </div>

    <div class="rule-thin"></div>
    <div class="green-band"></div>

    <div class="socials">
      <p class="socials__title">Vine Hollow Excursions</p>
      <p class="socials__row">/vinehollowexcursions <span class="socials__mark"></span></p>
      <p class="socials__row">@vinehollowexcursions <span class="socials__mark"></span></p>
      <p class="socials__row">/biz/vinehollowexcursions <span class="socials__mark"></span></p>
      <p class="socials__row">@coastalcellarrides <span class="socials__mark"></span></p>
    </div>

    <div class="contacts">
      <p class="contacts__row">
        <svg class="contacts__icon" viewBox="0 0 16 16" aria-hidden="true">
          <circle cx="8" cy="8" r="8" fill="#d9c8b0"/>
          <path d="M5.5 4.5l1.5 0 .6 1.8-.9.7c.4.9 1.1 1.6 2 2l.7-.9 1.8.6v1.5c-3.3.2-5.9-2.4-5.7-5.7z" fill="#436b4b"/>
        </svg>
        805-219-6384
      </p>
      <p class="contacts__row">
        <svg class="contacts__icon" viewBox="0 0 16 16" aria-hidden="true">
          <circle cx="8" cy="8" r="8" fill="#d9c8b0"/>
          <rect x="4.3" y="5.3" width="7.4" height="5.4" fill="none" stroke="#436b4b" stroke-width="1"/>
          <path d="M4.3 5.3L8 8.3l3.7-3" fill="none" stroke="#436b4b" stroke-width="1"/>
        </svg>
        info@vinehollowexcursions.example
      </p>
      <p class="contacts__row contacts__site">
        <svg class="contacts__icon" viewBox="0 0 16 16" aria-hidden="true">
          <circle cx="8" cy="8" r="8" fill="#d9c8b0"/>
          <circle cx="8" cy="8" r="3.6" fill="none" stroke="#436b4b" stroke-width="1"/>
          <path d="M4.4 8h7.2M8 4.4c-1.5 2.2-1.5 5 0 7.2M8 4.4c1.5 2.2 1.5 5 0 7.2" fill="none" stroke="#436b4b" stroke-width="0.8"/>
        </svg>
        <span>www.<strong>vinehollowexcursions</strong>.example</span>
      </p>
    </div>
  </section>

</body>
</html>
```